Homemaking training schools needs a Business Card design

Designer, Hello!

No special requirements, good-looking enough.
--------------------------------------------------------------------------

Name: Marcus Dole
Chairman
Tel: 0574-71948263
Mobile: 13857420916
Email: kelvora@mailnest.example
Web: www.prt2019.example
Add: No.258, LanpingJie, BeiyuanQu, Ningbo, Zhejiang

LOGO
Ningbo PRT Homemaking Training School

Target Market(s)

pregnant women, mothers, infants, the elderly and families, including cleaning, cooking, nursing training.

Industry/Entity Type

Business

Contact Information for Business Card

Name: Marcus Dole
Chairman
Tel: 0574-71948263
Mobile: 13857420916
Email: kelvora@mailnest.example
Web: www.prt2019.example

LOGO

Font styles to use
Serif
Sans Serif
Decorative

Requirements
Nice to have
• Feels: clean, specifications, safety, comfort, warmth and happiness.

```html
<!DOCTYPE html>
<html lang="en">
<head>
<meta charset="utf-8">
<title>PingRuiTang Business Card</title>
<link href="https://fonts.googleapis.com/css2?family=Montserrat:wght@500;600;700;800&display=swap" rel="stylesheet">
<style>
  :root {
    --blue: #1a73bd;
    --pink: #e6008a;
    --charcoal: #3a3a3a;
    --paper: #ffffff;
    --backdrop: #e9e9ec;
  }
  html, body {
    margin: 0;
    width: 1200px;
    height: 900px;
    overflow: hidden;
    background: var(--backdrop);
    font-family: "Montserrat", Arial, sans-serif;
  }
  .canvas {
    position: relative;
    width: 1200px;
    height: 900px;
  }
  .card {
    position: absolute;
    left: 260px;
    width: 680px;
    height: 390px;
    background: var(--paper);
    border-radius: 26px;
    overflow: hidden;
    box-shadow: 0 6px 22px rgba(0,0,0,0.12);
  }
  .card--front { top: 40px; }
  .card--back { top: 470px; }

  /* Front */
  .brand {
    position: absolute;
    left: 0; right: 0;
    top: 140px;
    display: flex;
    align-items: center;
    justify-content: center;
    gap: 14px;
  }
  .brand__dot {
    width: 26px; height: 26px;
    border-radius: 50%;
    background: var(--pink);
  }
  .brand__name {
    font-size: 54px;
    font-weight: 700;
    color: var(--blue);
    letter-spacing: -1px;
  }
  .front__web {
    position: absolute;
    left: 0; right: 0;
    top: 230px;
    text-align: center;
    font-size: 22px;
    font-weight: 700;
    color: var(--pink);
  }

  /* Back */
  .back__band {
    position: absolute;
    right: 0; top: 0;
    width: 280px; height: 390px;
  }
  .contact {
    position: absolute;
    left: 50px;
    bottom: 48px;
    color: var(--blue);
  }
  .contact__name {
    margin: 0;
    font-size: 30px;
    font-weight: 800;
    letter-spacing: 0.5px;
  }
  .contact__role {
    margin: 0 0 10px 18px;
    font-size: 15px;
    font-weight: 700;
    color: var(--pink);
  }
  .contact__address {
    margin: 0 0 8px 36px;
    font-size: 16px;
    font-weight: 600;
    line-height: 1.3;
  }
  .contact__list {
    list-style: none;
    margin: 0 0 0 36px;
    padding: 0;
    font-size: 16px;
    font-weight: 600;
    line-height: 1.45;
  }
  .contact__list li {
    display: flex;
    align-items: center;
    gap: 10px;
  }
  .contact__list svg {
    width: 13px; height: 13px;
    fill: none;
    stroke: var(--pink);
    stroke-width: 2;
  }
</style>
</head>
<body>
<div class="canvas">

  <section class="card card--front">
    <div class="brand">
      <span class="brand__dot"></span>
      <span class="brand__name">PingRuiTang</span>
    </div>
    <div class="front__web">www.prt2019.example</div>
  </section>

  <section class="card card--back">
    <svg class="back__band" viewBox="0 0 280 390" aria-hidden="true">
      <path d="M80 0 H280 V390 H250 C250 240 170 120 80 0 Z" fill="var(--charcoal)"/>
    </svg>
    <div class="contact">
      <h1 class="contact__name">MARCUS DOLE</h1>
      <p class="contact__role">CHAIRMAN</p>
      <p class="contact__address">258, LanpingJie<br>BeiyuanQu, Ningbo, Zhejiang</p>
      <ul class="contact__list">
        <li><svg viewBox="0 0 14 14"><path d="M3 1 L5 4 L4 6 Q6 9 8 10 L10 9 L13 11 L11 13 Q4 12 1 3 Z"/></svg>0574-71948263</li>
        <li><svg viewBox="0 0 14 14"><rect x="3" y="1" width="8" height="12" rx="1.5"/></svg>13857420916</li>
        <li><svg viewBox="0 0 14 14"><rect x="1" y="3" width="12" height="8"/><path d="M1 3 L7 8 L13 3"/></svg>kelvora@mailnest.example</li>
        <li><svg viewBox="0 0 14 14"><circle cx="7" cy="7" r="6"/><path d="M1 7 H13 M7 1 Q3 7 7 13 Q11 7 7 1"/></svg>www.prt2019.example</li>
      </ul>
    </div>
  </section>

</div>
</body>
</html>
```